Catering Menu Package

I currently have a complete menu package, which we have redesigned as far as content, now I need to it put together in a catalog type format. It is essentially 10-12 pages in length, and will be sent for print production. Upon receiving a final edit
Updates

I have added an example gif to the project.

I did this free hand this basically what I am looking for. please change text and type to whatever you think would look best. This is a total rough design so, feel free to change any and everything. The text for the page is on the word documents. If you need more images let me know I am in the process of getting as many images uploaded for your use.

Project Deadline Extended
Reason: I figured we got a late jump with questions, so i am extending a few days .

Target Market(s)

The target market is business who wish to have catered luncheons, breakfasts , meetings

Industry/Entity Type

Catering

Requirements
Must have
• I have attached a copy of the text that what we want in the package, our logo, and i have also attached a catering package of another company to give you an idea what the finished product will be
Should not have
• It should not look identical to the example catering packages, these are for some inspiration we want our own design with the same type of look and feel

```html
<!DOCTYPE html>
<html lang="en">
<head>
<meta charset="utf-8">
<title>Hot Entrees</title>
<link rel="stylesheet" href="https://fonts.googleapis.com/css2?family=Alegreya+Sans:wght@400&family=Parisienne&display=swap">
<style>
  :root {
    --paper: #ece6d8;
    --paper-edge: #e4ddcc;
    --ink: #1d1a16;
    --photo-warm: #7a4a22;
    --photo-dark: #3a2412;
    --photo-green: #4f5a2a;
  }
  * { margin: 0; padding: 0; box-sizing: border-box; }
  html, body { width: 1200px; height: 928px; overflow: hidden; background: #fff; }
  .page {
    position: relative;
    width: 1200px;
    height: 928px;
    overflow: hidden;
    background: var(--paper);
    font-family: "Alegreya Sans", sans-serif;
    color: var(--ink);
  }
  .buffet-photo {
    position: absolute;
    left: 0; top: 0;
    width: 366px; height: 928px;
    background:
      radial-gradient(ellipse at 30% 20%, #a86a30 0%, transparent 55%),
      radial-gradient(ellipse at 60% 70%, #8a3a2a 0%, transparent 50%),
      linear-gradient(170deg, var(--photo-warm) 0%, var(--photo-green) 35%, var(--photo-dark) 65%, #b07a3a 100%);
  }
  .menu-panel {
    position: absolute;
    left: 366px; top: 0;
    width: 834px; height: 928px;
    background: linear-gradient(180deg, var(--paper) 0%, var(--paper-edge) 100%);
  }
  .section-title {
    position: absolute;
    left: 376px; top: 22px;
    font-family: "Parisienne", cursive;
    font-size: 38px;
    line-height: 1;
    color: transparent;
    -webkit-text-stroke: 1px var(--ink);
  }
  .menu-item {
    position: absolute;
    left: 376px;
    width: 806px;
    font-size: 16.5px;
    line-height: 20.3px;
  }
  .line {
    display: flex;
    justify-content: space-between;
    white-space: nowrap;
  }
  .price { margin-left: 12px; }
</style>
</head>
<body>
<div class="page">
  <div class="buffet-photo" role="img" aria-label="Photo of a catered buffet display with fruit, bread and greenery"></div>
  <div class="menu-panel"></div>

  <h1 class="section-title">Hot Entrees</h1>

  <div class="menu-item" style="top:60px">
    <div class="line"><span>Chesapeake Crab Cake-</span></div>
    <div class="line"><span>6oz Jumbo Lump Crab Cake served with House-made Remoulade Oven Roasted Redskin Potatoes,</span></div>
    <div class="line"><span>&nbsp;and Sautéed Local Corn.</span><span class="price">$&amp;.&amp;&amp;</span></div>
  </div>

  <div class="menu-item" style="top:142px">
    <div class="line"><span>Key West Grilled Salmon-</span></div>
    <div class="line"><span>served with Pina-Colada Jeweled Rice, Fire-Roasted Seasonal Vegetable Medley, and Fresh Mango Salsa.</span></div>
    <div class="line"><span>Tropical Grilled Chicken-Jamaican Jerk Rubbed Chicken Breast grilled and topped with Fresh Mango Salsa,</span></div>
    <div class="line"><span>served with Roasted Seasonal Vegetable Medley, Jeweled Jasmine Rice, Pineapple Hawaiian Cole Slaw.</span></div>
    <div class="line"><span></span><span class="price">$&amp;.&amp;&amp;</span></div>
    <div class="line"><span>Add Cilantro Grilled Mahi-Mahi and Fresh Mango Salsa</span><span class="price">$&amp;.&amp;&amp;</span></div>
  </div>

  <div class="menu-item" style="top:284px">
    <div class="line"><span>Fried Chicken Picnic-</span></div>
    <div class="line"><span>Country Fried 8-cut Chicken served with Potato Salad, Pasta-Vegetable Salad, Creamy Cole Slaw, and Fresh</span></div>
    <div class="line"><span>Watermelon Wedge.</span><span class="price">$&amp;.&amp;&amp;</span></div>
  </div>

  <div class="menu-item" style="top:366px">
    <div class="line"><span>Chicken Parmesan-</span></div>
    <div class="line"><span>Lightly Breaded Chicken Breast, golden fried, and topped with Chef-crafted Marinara,</span></div>
    <div class="line"><span>&nbsp;Melted Provolone and Mozzarella, and served with Penne Pasta.</span><span class="price">$&amp;.&amp;&amp;</span></div>
  </div>

  <div class="menu-item" style="top:448px">
    <div class="line"><span>Fajita Lunch-</span></div>
    <div class="line"><span>Your choice of grilled Chicken breast strips or grilled Sirloin Steak strips, with Fire-Roasted Peppers</span></div>
    <div class="line"><span>and Onions, Flour Tortillas, Cuban Stewed Black Beans, Spanish Rice, and Fire-Roasted Seasonal</span></div>
    <div class="line"><span>Vegetable Medley. Diced Tomatoes, Salsa, Sour Cream, Crisp Lettuce, Shredded Cheese, and Jalapeño Garni.</span></div>
    <div class="line"><span></span><span class="price">$&amp;.&amp;&amp;</span></div>
    <div class="line"><span>Make it a Chicken and Beef Combo</span><span class="price">$&amp;.&amp;&amp;</span></div>
    <div class="line"><span>Add Fresh Made Guacamole</span><span class="price">$&amp;.&amp;&amp;</span></div>
  </div>

  <div class="menu-item" style="top:612px">
    <div class="line"><span>Chef-Made Italian Sausage Lasagna-</span></div>
    <div class="line"><span>&nbsp;Fresh Pasta, stacked high and layered with Ricotta, Italian Sausage, House Made Marinara and</span></div>
    <div class="line"><span>Provolone and Mozzarella Cheeses.</span><span class="price">$&amp;.&amp;&amp;</span></div>
  </div>

  <div class="menu-item" style="top:694px">
    <div class="line"><span>Ragn’ Cajun Lunch-</span></div>
    <div class="line"><span>Cajun Rubbed and Bourbon Sauce Basted 8-cut Chicken Served with Red Beans and Rice and Lemon Scented</span></div>
    <div class="line"><span>Petit Green Beans.</span><span class="price">$&amp;.&amp;&amp;</span></div>
  </div>

  <div class="menu-item" style="top:776px">
    <div class="line"><span>Grilled Vegetable Lasagna-</span></div>
    <div class="line"><span>Fresh Pasta,stacked high and layered with Ricotta, Grilled Seasonal Vegetables, House Made Marinara and</span></div>
    <div class="line"><span>Provolone and Mozzarella Cheeses.</span><span class="price">$&amp;.&amp;&amp;</span></div>
  </div>

  <div class="menu-item" style="top:858px">
    <div class="line"><span>Three Cheese Stuffed Shells-</span></div>
    <div class="line"><span>Served over Chef-Crafted Marinara with Balsamic Roasted Seasonal Vegetable Medley.</span><span class="price">$&amp;.&amp;&amp;</span></div>
  </div>
</div>
</body>
</html>
```